Logistics Website Design

See website https://tqfreightglobal.com for theme and color details. Need the site to be re-done and reflect some of the designs shown in this list here: https://pixelvane.com/tags/logistics-company-website

Target Market(s)

Logistics & Transportation

Industry/Entity Type

Logistics and Supply Chain

Coding

Number of Pages Required

5+ page

Requirements
Must have
• Colors must match theme of logo. Looking for a sleek, interactive design.

```html
<!DOCTYPE html>
<html lang="en">
<head>
<meta charset="utf-8">
<title>TQ Freight Global — Logistics</title>
<link href="https://fonts.googleapis.com/css2?family=Bebas+Neue&family=Lato:ital,wght@0,400;0,700;1,400&display=swap" rel="stylesheet">
<style>
:root{
  --black:#000;
  --panel:#111111;
  --card:#1b1b1b;
  --field:#1e1e1e;
  --orange:#ec6b42;
  --orange-light:#f4916a;
  --white:#ffffff;
  --muted:#d9d9d9;
  --line:#3a3a3a;
}
*{box-sizing:border-box;margin:0;padding:0}
html,body{width:1200px;height:3643px;overflow:hidden;background:var(--black)}
body{font-family:'Lato',sans-serif;color:var(--white);position:relative}
.display{font-family:'Bebas Neue',sans-serif;font-weight:400;letter-spacing:.5px}
.btn{display:inline-flex;align-items:center;justify-content:center;background:linear-gradient(180deg,var(--orange-light),var(--orange));border:2px solid #f6c2ad;border-radius:6px;color:#1a1a1a;font-weight:700;font-size:16px}
section,header,footer{position:absolute;left:0;width:1200px}

/* header */
.site-header{top:0;height:102px;background:var(--black)}
.brand{position:absolute;left:110px;top:33px;display:flex;align-items:center;gap:10px;color:var(--orange);font-weight:700;font-size:18px}
.brand-dot{width:28px;height:28px;border-radius:50%;background:var(--orange)}
.nav{position:absolute;left:445px;top:40px;display:flex;gap:30px;font-size:15px}
.header-cta{position:absolute;left:954px;top:27px;width:134px;height:49px}

/* hero */
.hero{top:102px;height:584px;border-bottom:1px solid #b8734f}
.hero-photo{position:absolute;inset:0;background:linear-gradient(180deg,#3d4450 0%,#8a5a48 30%,#e08a4e 52%,#6b4030 70%,#2a2522 100%)}
.hero-title{position:absolute;left:643px;top:170px;font-size:58px;line-height:60px;width:460px}
.hero-sub{position:absolute;left:643px;top:309px;font-size:17px;font-weight:700}
.hero-cta{position:absolute;left:643px;top:363px;width:177px;height:49px}
.hero-arrows{position:absolute;left:570px;top:506px;display:flex;gap:8px}

/* intro */
.intro{top:686px;height:463px;background:var(--black)}
.intro h2{position:absolute;left:110px;top:84px;font-size:38px}
.intro p{position:absolute;left:110px;top:150px;width:445px;font-size:14.5px;line-height:25.7px;text-align:justify}
.intro .btn{position:absolute;left:110px;top:327px;width:144px;height:50px}
.intro-photo{position:absolute;left:643px;top:87px;width:445px;height:290px;border-radius:6px;background:linear-gradient(160deg,#cfc6b6 0%,#a9a69a 45%,#6d6452 75%,#8c7b58 100%)}

/* services */
.services{top:1149px;height:499px;background:var(--panel)}
.section-title{position:absolute;left:0;width:1200px;text-align:center;font-size:38px}
.services .section-title{top:76px}
.service-row{position:absolute;left:112px;top:151px;display:flex;gap:24px}
.service-card{width:226px;height:261px;background:var(--card);border-radius:6px;text-align:center;padding:20px 18px 0}
.icon-circle{width:60px;height:60px;border-radius:50%;background:linear-gradient(180deg,var(--orange-light),var(--orange));margin:0 auto;display:flex;align-items:center;justify-content:center}
.card-title{font-size:18px;margin-top:16px}
.card-text{font-size:14px;line-height:26px;margin-top:10px;height:78px;overflow:hidden}
.read-more{display:block;font-size:13px;font-style:italic;text-decoration:underline;margin-top:12px}

/* story */
.story{top:1648px;height:438px;background:var(--black)}
.story .section-title{top:76px}
.story p{position:absolute;left:165px;top:142px;width:870px;text-align:center;font-size:14px;line-height:25.8px}
.story .btn{position:absolute;left:527px;top:302px;width:144px;height:50px}

/* industries */
.industries{top:2086px;height:540px;background:var(--panel)}
.industries .section-title{top:76px}
.industry-row{position:absolute;left:112px;top:157px;display:flex;gap:29px}
.industry-card{width:306px;height:297px;background:var(--card);border-radius:6px;text-align:center;padding:24px 20px 0}
.industry-card .card-text{height:104px}
.slider-arrow{position:absolute;top:292px;font-size:34px;font-weight:700;line-height:1}

/* contact */
.contact{top:2626px;height:652px;background:var(--black)}
.contact .section-title{top:76px}
.contact-sub{position:absolute;left:0;width:1200px;top:147px;text-align:center;font-size:15px}
.contact-form{position:absolute;left:112px;top:208px;width:976px;height:405px;background:var(--card);border-radius:6px}
.field{position:absolute;border:1px solid #6a6a6a;border-radius:6px;background:var(--field);display:flex;align-items:center;gap:10px;padding-left:22px;color:#bdbdbd;font-size:14.5px}
.field.tall{align-items:flex-start;padding-top:14px}
.contact-form .btn{position:absolute;left:415px;top:323px;width:144px;height:49px}

/* footer */
.site-footer{top:3278px;height:365px;background:var(--black)}
.footer-brand{position:absolute;left:113px;top:112px;display:flex;align-items:center;gap:10px;color:var(--orange);font-weight:700;font-size:22px}
.socials{position:absolute;left:176px;top:253px;display:flex;gap:12px}
.social{width:22px;height:22px;border-radius:50%;background:var(--white)}
.foot-col{position:absolute;top:56px}
.foot-col h3{font-weight:400;font-size:18px;margin-bottom:14px}
.foot-col ul{list-style:none}
.foot-col li{font-size:14px;line-height:34px;display:flex;align-items:center;gap:14px}
.foot-col li::before{content:"";width:7px;height:7px;border-radius:50%;background:var(--white);flex:none}
.contact-list li::before{display:none}
.contact-list li{align-items:flex-start;line-height:24px;margin-bottom:18px;gap:8px}
.footer-rule{position:absolute;left:112px;top:307px;width:976px;height:1px;background:var(--line)}
.copyright{position:absolute;left:0;width:1200px;top:320px;text-align:center;font-size:14px}
</style>
</head>
<body>

<header class="site-header">
  <div class="brand"><span class="brand-dot"></span>TQ Freight Global</div>
  <nav class="nav"><span>Home</span><span>Services</span><span>Industries</span><span>Request a Quote</span><span>About Us</span></nav>
  <span class="btn header-cta">Contact Us</span>
</header>

<section class="hero">
  <div class="hero-photo" role="img" aria-label="Photo of a white box truck driving on a highway at sunset"></div>
  <h1 class="hero-title display">Delivering Strength in Every Mile</h1>
  <p class="hero-sub">Secure and reliable transportation for all your cargo needs.</p>
  <span class="btn hero-cta">Request a Quote</span>
  <div class="hero-arrows">
    <svg width="26" height="26" viewBox="0 0 26 26"><circle cx="13" cy="13" r="11.5" fill="none" stroke="#fff" stroke-width="1.6"/><path d="M18 13H8M12 9l-4 4 4 4" fill="none" stroke="#fff" stroke-width="1.6"/></svg>
    <svg width="26" height="26" viewBox="0 0 26 26"><circle cx="13" cy="13" r="11.5" fill="none" stroke="#fff" stroke-width="1.6"/><path d="M8 13h10M14 9l4 4-4 4" fill="none" stroke="#fff" stroke-width="1.6"/></svg>
  </div>
</section>

<section class="intro">
  <h2 class="display">Keeping Your Supply Chain Moving</h2>
  <p>We deliver a comprehensive range of open-deck and specialized transportation services—including flatbed, step deck, heavy haul, and over-dimensional freight solutions. Backed by years of experience, a trusted nationwide carrier network, and a strong safety-first culture, we provide reliable, adaptable logistics support built around the unique requirements of every load.</p>
  <span class="btn">Read More</span>
  <div class="intro-photo" role="img" aria-label="Photo of a white semi truck on a rural highway"></div>
</section>

<section class="services">
  <h2 class="section-title display">Our Services</h2>
  <div class="service-row">
    <div class="service-card">
      <div class="icon-circle"><svg width="34" height="20" viewBox="0 0 34 20" fill="none" stroke="#fff" stroke-width="1.6"><path d="M2 13h30M6 8h20v5"/><rect x="24" y="4" width="7" height="9"/><circle cx="8" cy="16" r="2.5"/><circle cx="26" cy="16" r="2.5"/></svg></div>
      <div class="card-title display">Flatbed Transportation</div>
      <div class="card-text">From routine shipments to oversized and heavy-haul loads, we handle freight with care and precision every time.</div>
      <span class="read-more">Read More</span>
    </div>
    <div class="service-card">
      <div class="icon-circle"><svg width="34" height="22" viewBox="0 0 34 22" fill="none" stroke="#fff" stroke-width="1.6"><rect x="2" y="3" width="20" height="11"/><path d="M6 3v11M10 3v11M14 3v11M18 3v11"/><path d="M22 7h6l4 4v5H2v-2"/><circle cx="8" cy="18" r="2.5"/><circle cx="26" cy="18" r="2.5"/></svg></div>
      <div class="card-title display">Step Deck Transportation</div>
      <div class="card-text">Our step deck trucking services support tall, heavy, and specialized freight that needs extra clearance.</div>
      <span class="read-more">Read More</span>
    </div>
    <div class="service-card">
      <div class="icon-circle"><svg width="32" height="22" viewBox="0 0 32 22" fill="none" stroke="#fff" stroke-width="1.6"><rect x="2" y="3" width="18" height="12"/><path d="M20 7h6l4 4v4H20"/><circle cx="8" cy="17" r="2.5"/><circle cx="25" cy="17" r="2.5"/></svg></div>
      <div class="card-title display">Dry Van Transportation</div>
      <div class="card-text">From consumer goods to industrial materials, our dry van services provide the protection your cargo needs.</div>
      <span class="read-more">Read More</span>
    </div>
    <div class="service-card">
      <div class="icon-circle"><svg width="34" height="22" viewBox="0 0 34 22" fill="none" stroke="#fff" stroke-width="1.6"><rect x="4" y="4" width="14" height="9" rx="4"/><path d="M2 15h30M18 8h7l5 4v3"/><circle cx="8" cy="18" r="2.5"/><circle cx="26" cy="18" r="2.5"/></svg></div>
      <div class="card-title display">Heavy Haul Transportation</div>
      <div class="card-text">We provide heavy haul trucking solutions for oversized, overweight, and complex loads across the country.</div>
      <span class="read-more">Read More</span>
    </div>
  </div>
</section>

<section class="story">
  <h2 class="section-title display">Our Story</h2>
  <p>TQ Freight Global™ was born out of real-world experience in the fitness equipment industry. What started as a company shipping strength equipment, cardio machines, and training gear to gyms, schools, and commercial facilities quickly evolved into something bigger. As order volume grew and supply chains became more complex, the team developed deep expertise in coordinating freight, managing deliveries, and navigating the challenges of large-scale equipment transportation. That hands-on experience laid the foundation for what would eventually become a full-service logistics operation.</p>
  <span class="btn">Read More</span>
</section>

<section class="industries">
  <h2 class="section-title display">Industries</h2>
  <span class="slider-arrow" style="left:40px">«</span>
  <span class="slider-arrow" style="left:1134px">»</span>
  <div class="industry-row">
    <div class="industry-card">
      <div class="icon-circle"><svg width="24" height="26" viewBox="0 0 24 26" fill="none" stroke="#fff" stroke-width="1.8"><path d="M5 8h14l-2 16H7z"/><path d="M4 8h16M12 8V2l4-1"/></svg></div>
      <div class="card-title display">Food &amp; Beverage</div>
      <div class="card-text">TQ Freight Global provides reliable, compliant, and efficient trucking solutions for the food and beverage industry. We specialize in transporting food products, ingredients and more.</div>
      <span class="read-more">Read More</span>
    </div>
    <div class="industry-card">
      <div class="icon-circle"><svg width="24" height="26" viewBox="0 0 24 26" fill="none" stroke="#fff" stroke-width="1.8"><path d="M4 9h16l-1 15H5z"/><path d="M8 9V6a4 4 0 0 1 8 0v3"/></svg></div>
      <div class="card-title display">E-Commerce &amp; Retail</div>
      <div class="card-text">Our E-Commerce &amp; Retail Trucking Services are designed to support the fast-paced logistics demands of modern online retailers, marketplaces, and stores.</div>
      <span class="read-more">Read More</span>
    </div>
    <div class="industry-card">
      <div class="icon-circle"><svg width="28" height="24" viewBox="0 0 28 24" fill="none" stroke="#fff" stroke-width="1.8"><path d="M2 22V10l7 4v-4l7 4v-4l7 4V2h3v20z"/></svg></div>
      <div class="card-title display">Manufacturing</div>
      <div class="card-text">TQ Freight Global provides reliable, compliant, and efficient trucking solutions for the manufacturing industry. We specialize in transporting raw materials, parts and machinery.</div>
      <span class="read-more">Read More</span>
    </div>
  </div>
</section>

<section class="contact">
  <h2 class="section-title display">Let's Move Your Business Forward</h2>
  <p class="contact-sub">Let's discuss your logistics needs and how we can help your business thrive</p>
  <div class="contact-form">
    <div class="field" style="left:25px;top:35px;width:448px;height:47px"><svg width="14" height="15" viewBox="0 0 14 15" fill="#bdbdbd"><circle cx="7" cy="4" r="3.5"/><path d="M0 15a7 6 0 0 1 14 0z"/></svg>Name</div>
    <div class="field" style="left:498px;top:35px;width:448px;height:47px"><svg width="14" height="15" viewBox="0 0 14 15" fill="#bdbdbd"><circle cx="7" cy="4" r="3.5"/><path d="M0 15a7 6 0 0 1 14 0z"/></svg>Last Name</div>
    <div class="field" style="left:25px;top:102px;width:448px;height:49px"><svg width="17" height="12" viewBox="0 0 17 12" fill="none" stroke="#bdbdbd" stroke-width="1.5"><rect x="1" y="1" width="15" height="10"/><path d="M1 1l7.5 6L16 1"/></svg>Email</div>
    <div class="field" style="left:498px;top:102px;width:448px;height:49px"><svg width="15" height="15" viewBox="0 0 15 15" fill="#bdbdbd"><path d="M3 1l3 3-2 2a9 9 0 0 0 5 5l2-2 3 3-2 2C6 14 1 9 1 3z"/></svg>Phone Number</div>
    <div class="field tall" style="left:25px;top:170px;width:921px;height:116px"><svg width="17" height="12" viewBox="0 0 17 12" fill="none" stroke="#bdbdbd" stroke-width="1.5" style="margin-top:3px"><rect x="1" y="1" width="15" height="10"/><path d="M1 1l7.5 6L16 1"/></svg>Message</div>
    <span class="btn">Submit</span>
  </div>
</section>

<footer class="site-footer">
  <div class="footer-brand"><span class="brand-dot" style="width:34px;height:34px"></span>TQ Freight Global</div>
  <div class="socials"><span class="social"></span><span class="social"></span></div>
  <div class="foot-col" style="left:401px">
    <h3>Quick Links</h3>
    <ul><li>Home</li><li>Services</li><li>Request a Quote</li><li>About Us</li><li>Contact</li></ul>
  </div>
  <div class="foot-col" style="left:605px">
    <h3>Our Services</h3>
    <ul><li>Flatbed Transportation</li><li>Step Deck Transportation</li><li>Dry Van Transportation</li><li>Heavy Haul Transportation</li></ul>
  </div>
  <div class="foot-col" style="left:885px;width:220px">
    <h3>Contact Us</h3>
    <ul class="contact-list">
      <li><svg width="16" height="18" viewBox="0 0 16 18" style="flex:none;margin-top:3px"><path d="M8 1a6 6 0 0 1 6 6c0 4-6 10-6 10S2 11 2 7a6 6 0 0 1 6-6z" fill="#fff"/><circle cx="8" cy="7" r="2.2" fill="#000"/></svg>Suite 210, 480 Harbor Line Rd, Newark, NJ 07105</li>
      <li><svg width="16" height="16" viewBox="0 0 16 16" style="flex:none;margin-top:4px"><circle cx="8" cy="8" r="8" fill="#fff"/><rect x="4" y="5" width="8" height="6" fill="none" stroke="#000" stroke-width="1.2"/></svg>hello@tqfreightglobal.com</li>
      <li><svg width="16" height="16" viewBox="0 0 16 16" style="flex:none;margin-top:4px"><circle cx="8" cy="8" r="8" fill="#fff"/><path d="M5 4l2 2-1 1a5 5 0 0 0 3 3l1-1 2 2-1 1c-4 0-7-3-7-7z" fill="#000"/></svg>+1 555 014 2270</li>
    </ul>
  </div>
  <div class="footer-rule"></div>
  <p class="copyright">© 2026 TQ Freight Global. All Rights Reserved.</p>
</footer>

</body>
</html>
```